Redesign Digital Lending Mobile App - Android/ Flutter

Want to re-theme an existing Digital Lending Mobile app to simplify customer journeys, as well as uplift the UI.

Most users will have small screen phones so the design needs to take that into consideration while also adapting to those with larger devices, like admins with Tablets.

Have already laid out customer journeys on Figma with guidance on how the flow of the app should be. https://www.plankora.example/board/q4ZtRm81KdWe7YhXcvBnaL/LoomKit?frame-id=3-5182&s=Jk2pQwEr7TyUi-9

Video capture of current app: https://vaultbin.example/clip/7Hx3LmQp9RtZw2KcVn4YsBd8EfGj1/play
https://vaultbin.example/clip/4PsWq8ZnTk2LrXy6MbJc3VhGd9FeA/play

The documented views for Web are also here https://docshelf.example/open?ref=3B8F2204AD7C91E5!tk8d1f6a2c4e7b90d3f5a1c8e2b6d4f9a07&cid=3b8f2204ad7c91e5&kind=file%2Cdocx&wdo=2

Target Market(s)

Kenya, Tanzania, Uganda - Africa

Industry/Entity Type

Fintech

Requirements
Must have
• Responsive for diff screens, esp. in context of smaller screen smartphone
Nice to have
• Thematic components to ensure new views can easily be adapted to these themse

```html
<!DOCTYPE html>
<html lang="en">
<head>
<meta charset="utf-8">
<title>Lending App Screens</title>
<link href="https://fonts.googleapis.com/css2?family=Lato:wght@400;700&display=swap" rel="stylesheet">
<style>
:root{
  --page:#dadada;
  --screen:#f5f6fa;
  --ink:#1c1c1c;
  --muted:#444;
  --line:#e2e4ea;
  --blue:#3777c8;
  --track:#d9e1f7;
  --green:#4a9f68;
  --teal:#3c9ea8;
  --panel:#ffffff;
  --stripe:#eef0f5;
}
*{box-sizing:border-box;margin:0;padding:0}
html,body{width:1200px;height:598px;overflow:hidden;background:var(--page);font-family:'Lato',sans-serif;color:var(--ink)}
.stage{position:absolute;left:0;top:0;width:2024px;height:1008px;transform:scale(0.59289);transform-origin:0 0}
.screen{position:absolute;width:392px;height:844px;background:var(--screen);border-radius:52px;overflow:hidden;box-shadow:0 2px 10px rgba(0,0,0,.05)}
.title{position:absolute;left:0;right:0;top:34px;text-align:center;font-size:25px;font-weight:400;letter-spacing:.2px}
.menu-icon{position:absolute;left:346px;top:38px;width:28px;height:20px}
.divider{position:absolute;left:21px;right:19px;top:100px;height:1px;background:var(--line)}
.stats{position:absolute;left:21px;top:129px;display:flex;gap:12px}
.stat{width:78px;height:44px;background:#fff;border:1px solid var(--line);border-radius:3px;padding:6px 8px}
.stat-label{font-size:9px;color:var(--muted);white-space:nowrap}
.stat-value{font-size:11px;margin-top:6px}
.filter-btn{position:absolute;width:40px;height:32px;background:#fff;border:1px solid #cfd6de;border-radius:3px;display:flex;align-items:center;justify-content:center;box-shadow:0 1px 2px rgba(0,0,0,.1)}
.metric{position:absolute;left:21px;right:19px;font-size:15px;display:flex;justify-content:space-between}
.track{position:absolute;left:21px;width:352px;height:7px;background:var(--track);border-radius:4px}
.fill{position:absolute;left:0;top:0;width:121px;height:7px;background:var(--blue);border-radius:4px}
.knob{position:absolute;left:112px;top:-6px;width:19px;height:19px;border-radius:50%;background:#fff;border:1.5px solid var(--blue)}
.reports{position:absolute;left:21px;top:618px;font-size:16px}
.chart{position:absolute;left:21px;top:640px;width:240px;height:140px}
.next{position:absolute;color:#fff;font-weight:700;border-radius:20px;background:linear-gradient(90deg,#3e9f6d,#3a78c2);display:flex;align-items:center;justify-content:center;box-shadow:0 3px 6px rgba(0,0,0,.15)}
.next-sm{left:294px;top:742px;width:78px;height:28px;font-size:14px}
.side-menu{position:absolute;left:227px;top:0;width:160px;height:396px;background:var(--panel);border:1px solid #cfd6de;border-bottom-color:var(--teal)}
.side-item{position:absolute;right:20px;display:flex;align-items:center;gap:10px;font-size:14px}
.dropdown{position:absolute;background:var(--panel);border:1px solid #c9d0d8;box-shadow:0 2px 6px rgba(0,0,0,.08)}
.dd-item{position:absolute;left:17px;font-size:14px;white-space:nowrap}
.table{position:absolute;left:56px;top:230px;width:279px;background:#fff;box-shadow:0 1px 4px rgba(0,0,0,.06)}
.row{display:flex;height:46px;align-items:center;font-size:12px}
.row:nth-child(even){background:var(--stripe)}
.cell-key{width:178px;padding-left:13px;border-right:1px solid var(--line);height:100%;display:flex;align-items:center}
.cell-val{padding-left:20px}
</style>
</head>
<body>
<div class="stage">

<!-- Screen 1: dashboard -->
<section class="screen" style="left:92px;top:78px">
  <h1 class="title">DASHBOARD</h1>
  <svg class="menu-icon" viewBox="0 0 28 20"><path d="M0 1h28M8 10h20M4 19h24" stroke="#222" stroke-width="2.4"/></svg>
  <div class="divider"></div>
  <div class="stats">
    <div class="stat"><div class="stat-label">0 Disbursed</div><div class="stat-value">$ 30,000</div></div>
    <div class="stat"><div class="stat-label">0 Collected</div><div class="stat-value">$ 20,000</div></div>
    <div class="stat"><div class="stat-label">0 Active Client</div><div class="stat-value">$ 50</div></div>
    <div class="stat"><div class="stat-label">0 New Clients</div><div class="stat-value">$ 30</div></div>
  </div>
  <div class="filter-btn" style="left:21px;top:205px"><svg width="22" height="16" viewBox="0 0 22 16"><g stroke="#3c9ea8" stroke-width="1.4" fill="#fff"><path d="M1 3h20M1 8h20M1 13h20"/><circle cx="14" cy="3" r="2"/><circle cx="7" cy="8" r="2"/><circle cx="12" cy="13" r="2"/></g></svg></div>
  <div class="metric" style="top:276px"><span>Near Due</span><span>$ 25, 00, 000</span></div>
  <div class="track" style="top:310px"><div class="fill"></div><div class="knob"></div></div>
  <div class="metric" style="top:356px"><span>Due</span><span>$ 34, 000</span></div>
  <div class="track" style="top:393px"><div class="fill"></div><div class="knob"></div></div>
  <div class="metric" style="top:432px"><span>Pending Disbursement</span><span>$ 30, 000</span></div>
  <div class="track" style="top:473px"><div class="fill"></div><div class="knob"></div></div>
  <div class="metric" style="top:516px"><span>Active Loan</span><span>$ 20, 000</span></div>
  <div class="track" style="top:550px"><div class="fill"></div><div class="knob"></div></div>
  <div class="reports">Reports</div>
  <svg class="chart" viewBox="0 0 240 140"><g fill="#3777c8"><rect x="8" y="62" width="22" height="60"/><rect x="48" y="41" width="22" height="81"/><rect x="90" y="87" width="22" height="35"/><rect x="131" y="81" width="22" height="41"/></g><g fill="#4a9f68"><rect x="171" y="40" width="22" height="82"/><rect x="214" y="10" width="22" height="112"/></g><path d="M0 123h240" stroke="#ccc"/><g font-size="6" fill="#555" text-anchor="middle" font-family="Lato,sans-serif"><text x="19" y="133">F1</text><text x="59" y="133">F2</text><text x="101" y="133">F3</text><text x="142" y="133">F4</text><text x="182" y="133">F5</text><text x="225" y="133">F6</text></g></svg>
  <div class="next next-sm">Next</div>
</section>

<!-- Screen 2: dashboard with side menu -->
<section class="screen" style="left:574px;top:78px">
  <h1 class="title" style="left:-18px">DASHBOARD</h1>
  <div class="divider"></div>
  <div class="stats" style="left:15px">
    <div class="stat"><div class="stat-label">0 Disbursed</div><div class="stat-value">$ 30,000</div></div>
    <div class="stat"><div class="stat-label">0 Collected</div><div class="stat-value">$ 20,000</div></div>
    <div class="stat"><div class="stat-label">0 Active Client</div><div class="stat-value">$ 50</div></div>
  </div>
  <div class="filter-btn" style="left:15px;top:204px"><svg width="22" height="16" viewBox="0 0 22 16"><g stroke="#3c9ea8" stroke-width="1.4" fill="#fff"><path d="M1 3h20M1 8h20M1 13h20"/><circle cx="14" cy="3" r="2"/><circle cx="7" cy="8" r="2"/><circle cx="12" cy="13" r="2"/></g></svg></div>
  <div class="metric" style="top:275px;left:15px;right:21px"><span>Near Due</span><span>$ 25, 00, 000</span></div>
  <div class="track" style="top:309px;left:15px"><div class="fill"></div><div class="knob"></div></div>
  <div class="metric" style="top:355px;left:15px;right:21px"><span>Due</span><span>$ 34, 000</span></div>
  <div class="track" style="top:392px;left:15px"><div class="fill"></div><div class="knob"></div></div>
  <div class="metric" style="top:431px;left:15px;right:21px"><span>Pending Disbursement</span><span>$ 30, 000</span></div>
  <div class="track" style="top:472px;left:15px"><div class="fill"></div><div class="knob"></div></div>
  <div class="metric" style="top:515px;left:15px;right:21px"><span>Active Loan</span><span>$ 20, 000</span></div>
  <div class="track" style="top:549px;left:15px"><div class="fill"></div><div class="knob"></div></div>
  <div class="reports" style="left:15px">Reports</div>
  <svg class="chart" style="left:15px;top:639px" viewBox="0 0 240 140"><g fill="#3777c8"><rect x="8" y="62" width="22" height="60"/><rect x="48" y="41" width="22" height="81"/><rect x="90" y="87" width="22" height="35"/><rect x="131" y="81" width="22" height="41"/></g><g fill="#4a9f68"><rect x="171" y="40" width="22" height="82"/><rect x="214" y="10" width="22" height="112"/></g><path d="M0 123h240" stroke="#ccc"/><g font-size="6" fill="#555" text-anchor="middle" font-family="Lato,sans-serif"><text x="19" y="133">F1</text><text x="59" y="133">F2</text><text x="101" y="133">F3</text><text x="142" y="133">F4</text><text x="182" y="133">F5</text><text x="225" y="133">F6</text></g></svg>
  <div class="next next-sm" style="left:288px;top:741px">Next</div>
  <nav class="side-menu">
    <svg class="menu-icon" style="left:112px;top:37px" viewBox="0 0 28 20"><path d="M0 1h28M8 10h20M4 19h24" stroke="#222" stroke-width="2.4"/></svg>
    <div class="side-item" style="top:93px">Dashboard <svg width="11" height="11" viewBox="0 0 11 11" fill="#333"><rect width="4" height="4"/><rect x="6" width="4" height="4"/><rect y="6" width="4" height="4"/><rect x="6" y="6" width="4" height="4"/></svg></div>
    <div class="side-item" style="top:143px">Clients <svg width="11" height="12" viewBox="0 0 11 12" fill="#333"><circle cx="5.5" cy="3" r="3"/><path d="M0 12a5.5 5 0 0 1 11 0z"/></svg></div>
    <div class="side-item" style="top:193px">Groups <svg width="15" height="12" viewBox="0 0 15 12" fill="#333"><circle cx="7.5" cy="3" r="2.5"/><circle cx="2.5" cy="4" r="2"/><circle cx="12.5" cy="4" r="2"/><path d="M3 12a4.5 4.5 0 0 1 9 0zM0 11a2.5 3 0 0 1 4-3l-1 3zM15 11a2.5 3 0 0 0-4-3l1 3z"/></svg></div>
    <div class="side-item" style="top:243px">Centers <svg width="14" height="14" viewBox="0 0 14 14"><circle cx="7" cy="7" r="7" fill="#333"/><text x="7" y="11" fill="#fff" font-size="10" font-weight="700" text-anchor="middle" font-family="Lato,sans-serif">?</text></svg></div>
    <div class="side-item" style="top:293px">Profile <svg width="12" height="12" viewBox="0 0 12 12" fill="#333"><circle cx="5" cy="3" r="3"/><path d="M0 12a5 5 0 0 1 9-3l-2 3z"/><circle cx="10" cy="10" r="2"/></svg></div>
  </nav>
</section>

<!-- Screen 3: dashboard with filter dropdown -->
<section class="screen" style="left:1056px;top:78px">
  <h1 class="title">DASHBOARD</h1>
  <svg class="menu-icon" style="left:343px;top:37px" viewBox="0 0 28 20"><path d="M0 1h28M8 10h20M4 19h24" stroke="#222" stroke-width="2.4"/></svg>
  <div class="divider" style="left:18px;right:14px"></div>
  <div class="stats" style="left:18px;top:128px">
    <div class="stat"><div class="stat-label">0 Disbursed</div><div class="stat-value">$ 30,000</div></div>
    <div class="stat"><div class="stat-label">0 Collected</div><div class="stat-value">$ 20,000</div></div>
    <div class="stat"><div class="stat-label">0 Active Client</div><div class="stat-value">$ 50</div></div>
    <div class="stat"><div class="stat-label">0 New Clients</div><div class="stat-value">$ 30</div></div>
  </div>
  <div class="metric" style="top:275px;left:18px;right:22px"><span>Near Due</span><span>$ 25, 00, 000</span></div>
  <div class="track" style="top:309px;left:18px"><div class="fill"></div><div class="knob"></div></div>
  <div class="metric" style="top:355px;left:18px;right:22px"><span>Due</span><span>$ 34, 000</span></div>
  <div class="track" style="top:392px;left:18px"><div class="fill"></div><div class="knob"></div></div>
  <div class="metric" style="top:431px;left:18px;right:22px"><span>Pending Disbursement</span><span>$ 30, 000</span></div>
  <div class="track" style="top:472px;left:18px"><div class="fill"></div><div class="knob"></div></div>
  <div class="metric" style="top:515px;left:18px;right:22px"><span>Active Loan</span><span>$ 20, 000</span></div>
  <div class="track" style="top:549px;left:18px"><div class="fill"></div><div class="knob"></div></div>
  <div class="reports" style="left:18px">Reports</div>
  <svg class="chart" style="left:18px;top:639px" viewBox="0 0 240 140"><g fill="#3777c8"><rect x="8" y="62" width="22" height="60"/><rect x="48" y="41" width="22" height="81"/><rect x="90" y="87" width="22" height="35"/><rect x="131" y="81" width="22" height="41"/></g><g fill="#4a9f68"><rect x="171" y="40" width="22" height="82"/><rect x="214" y="10" width="22" height="112"/></g><path d="M0 123h240" stroke="#ccc"/><g font-size="6" fill="#555" text-anchor="middle" font-family="Lato,sans-serif"><text x="19" y="133">F1</text><text x="59" y="133">F2</text><text x="101" y="133">F3</text><text x="142" y="133">F4</text><text x="182" y="133">F5</text><text x="225" y="133">F6</text></g></svg>
  <div class="next next-sm" style="left:291px;top:741px">Next</div>
  <div class="dropdown" style="left:0;top:170px;width:133px;height:297px">
    <div class="filter-btn" style="left:17px;top:34px"><svg width="22" height="16" viewBox="0 0 22 16"><g stroke="#3c9ea8" stroke-width="1.4" fill="#fff"><path d="M1 3h20M1 8h20M1 13h20"/><circle cx="14" cy="3" r="2"/><circle cx="7" cy="8" r="2"/><circle cx="12" cy="13" r="2"/></g></svg></div>
    <div class="dd-item" style="top:97px">Loan officer</div>
    <div class="dd-item" style="top:147px">Branch</div>
    <div class="dd-item" style="top:197px">Fund</div>
    <div class="dd-item" style="top:247px">Product</div>
  </div>
</section>

<!-- Screen 4: loan summary -->
<section class="screen" style="left:1537px;top:80px">
  <h1 class="title" style="top:36px">LOAN SUMMARY</h1>
  <svg style="position:absolute;left:363px;top:40px" width="10" height="16" viewBox="0 0 10 16"><path d="M2 1l7 7-7 7" stroke="#222" stroke-width="1.6" fill="none"/></svg>
  <div class="divider" style="top:95px;left:20px;right:20px"></div>
  <div class="table">
    <div class="row"><div class="cell-key">Reference No 1</div><div class="cell-val">3213</div></div>
    <div class="row"><div class="cell-key">Loan status</div><div class="cell-val">Active</div></div>
    <div class="row"><div class="cell-key">Loan date</div><div class="cell-val" style="padding-left:0">13 Jul 2024</div></div>
    <div class="row"><div class="cell-key">Due date</div><div class="cell-val" style="padding-left:0">20 Jul 2024</div></div>
    <div class="row"><div class="cell-key">Next due</div><div class="cell-val" style="padding-left:0">27 Jul 2024</div></div>
    <div class="row"><div class="cell-key">Last due</div><div class="cell-val" style="padding-left:0">27 Jul 2024</div></div>
    <div class="row"><div class="cell-key">Principal</div><div class="cell-val" style="padding-left:0">$30,000</div></div>
    <div class="row"><div class="cell-key">Amount outstanding</div><div class="cell-val" style="padding-left:20px">$30,000</div></div>
    <div class="row"><div class="cell-key">Overdue Days</div><div class="cell-val" style="padding-left:20px">30</div></div>
  </div>
  <div class="dropdown" style="left:0;top:171px;width:136px;height:347px">
    <div class="filter-btn" style="left:21px;top:35px"><svg width="22" height="16" viewBox="0 0 22 16"><g stroke="#3c9ea8" stroke-width="1.4" fill="#fff"><path d="M1 3h20M1 8h20M1 13h20"/><circle cx="14" cy="3" r="2"/><circle cx="7" cy="8" r="2"/><circle cx="12" cy="13" r="2"/></g></svg></div>
    <div class="dd-item" style="top:92px;left:20px">Loan status</div>
    <div class="dd-item" style="top:142px;left:20px">Loan date</div>
    <div class="dd-item" style="top:192px;left:20px">Branch</div>
    <div class="dd-item" style="top:242px;left:20px">Fund</div>
    <div class="dd-item" style="top:292px;left:20px">Product</div>
  </div>
  <div class="dropdown" style="left:57px;top:293px;width:196px;height:270px">
    <div class="dd-item" style="top:27px;left:26px">Active Loans</div>
    <div class="dd-item" style="top:77px;left:26px">Near Due</div>
    <div class="dd-item" style="top:127px;left:26px">Overdue</div>
    <div class="dd-item" style="top:177px;left:26px">Pending disbursement</div>
    <div class="dd-item" style="top:227px;left:26px">Pending approval</div>
  </div>
  <div class="next" style="left:141px;top:680px;width:110px;height:42px;font-size:19px">Next</div>
</section>

</div>
</body>
</html>
```